Cognitive therapist.

I am a therapist and my main work is with clients who have depression and anxiety disorders.

I need something reasonably plain. Cognitive therapy is a very pragmatic approach to dealing with problems, so it isn't new agey (no offence to new age therapies at all)
Updates

Hi everyone, I am currently looking at a particular design that I will most likely go with. Cheers, Meg

Industry/Entity Type

Work

Contact Information for Business Card

Meg Tarvish
Cognitive Therapist
BA, PG Dip Mental Health,
PG Dip Cog Beh Therapy
MKTPR

The Quarry Lodge,
Level One
48 Marlow Parade
Cnr Fenwick St & Marlow Parade
P O Box 38 219
WELLINGTON 6143

Phone: 021 574 3082 Email: mtarvish@quellnet.co.nz

www.megtarvish.co.nz

Requirements
Should not have
• No illustration, or colour. not old style fonts.

```html
<!DOCTYPE html>
<html lang="en">
<head>
<meta charset="utf-8">
<title>Meg Tarvish – Business Card</title>
<link rel="stylesheet" href="https://fonts.googleapis.com/css2?family=Ubuntu:ital,wght@0,300;0,400;0,500;1,400&display=swap">
<style>
  :root {
    --backdrop: #8a5e3b;
    --paper: #ffffff;
    --paper-shade: #ecebe8;
    --brand-blue: #1a7fc4;
    --blue-light: #1a9ae0;
    --blue-deep: #0a5ea8;
    --ink-grey: #555555;
    --ink-dark: #444444;
    --white: #ffffff;
  }
  * { margin: 0; padding: 0; box-sizing: border-box; }
  html, body {
    width: 1200px;
    height: 864px;
    overflow: hidden;
    background: var(--backdrop);
    font-family: "Ubuntu", sans-serif;
  }
  .card {
    position: absolute;
    left: 100px;
    top: 157px;
    width: 1000px;
    height: 550px;
    background: radial-gradient(ellipse at 30% 40%, var(--paper) 45%, var(--paper-shade) 100%);
    overflow: hidden;
  }
  .card__swoosh {
    position: absolute;
    inset: 0;
    width: 1000px;
    height: 550px;
  }
  .headline {
    position: absolute;
    left: 68px;
    top: 62px;
  }
  .headline__name {
    font-size: 82px;
    font-weight: 500;
    color: var(--brand-blue);
    line-height: 1;
    letter-spacing: 1px;
  }
  .headline__role {
    margin-top: 8px;
    font-size: 30px;
    font-style: italic;
    color: var(--ink-dark);
  }
  .credentials {
    position: absolute;
    left: 68px;
    top: 362px;
  }
  .credentials__name {
    font-size: 35px;
    font-weight: 500;
    color: var(--brand-blue);
    margin-bottom: 8px;
  }
  .credentials__line {
    font-size: 26px;
    font-weight: 300;
    color: var(--ink-grey);
    line-height: 38px;
  }
  .contact {
    position: absolute;
    right: 48px;
    top: 200px;
    list-style: none;
    text-align: right;
  }
  .contact__item {
    display: flex;
    justify-content: flex-end;
    align-items: center;
    gap: 12px;
    font-size: 21px;
    font-weight: 500;
    color: var(--white);
    height: 36px;
  }
  .contact__icon { width: 26px; height: 26px; }
  .address {
    position: absolute;
    right: 52px;
    top: 405px;
    text-align: right;
    font-size: 19px;
    font-weight: 400;
    color: var(--white);
    line-height: 28px;
    font-style: normal;
  }
</style>
</head>
<body>
  <section class="card">
    <svg class="card__swoosh" viewBox="0 0 1000 550" aria-hidden="true">
      <defs>
        <linearGradient id="silver" x1="0" y1="0" x2="1" y2="1">
          <stop offset="0" stop-color="#f4f4f4"/>
          <stop offset="0.45" stop-color="#9a9a9a"/>
          <stop offset="0.7" stop-color="#e8e8e8"/>
          <stop offset="1" stop-color="#7c7c7c"/>
        </linearGradient>
        <linearGradient id="blue-field" x1="0" y1="1" x2="1" y2="0">
          <stop offset="0" stop-color="var(--blue-light)"/>
          <stop offset="1" stop-color="var(--blue-deep)"/>
        </linearGradient>
      </defs>
      <path d="M676 0 C690 250 560 470 370 550 L1000 550 L1000 0 Z" fill="url(#silver)"/>
      <path d="M704 0 C712 260 630 470 470 550 L1000 550 L1000 0 Z" fill="url(#blue-field)"/>
    </svg>

    <header class="headline">
      <h1 class="headline__name">Meg Tarvish</h1>
      <p class="headline__role">Cognitive Therapist in Wellington</p>
    </header>

    <div class="credentials">
      <h2 class="credentials__name">Meg Tarvish</h2>
      <p class="credentials__line">Cognitive Therapist BA,</p>
      <p class="credentials__line">PG Dip Mental Health,</p>
      <p class="credentials__line">PG Dip Cog Beh Therapy</p>
    </div>

    <ul class="contact">
      <li class="contact__item">021 574 3082
        <svg class="contact__icon" viewBox="0 0 26 26" aria-hidden="true">
          <circle cx="13" cy="13" r="12" fill="#dfe9f2"/>
          <path d="M8 7 l3 0 l1 4 l-2 1 q2 4 5 5 l1 -2 l4 1 l0 3 q-10 1 -12 -12 z" fill="#3a6f9c"/>
        </svg>
      </li>
      <li class="contact__item">mtarvish@quellnet.co.nz
        <svg class="contact__icon" viewBox="0 0 26 26" aria-hidden="true">
          <circle cx="13" cy="13" r="12" fill="#dfe9f2"/>
          <rect x="6" y="8" width="14" height="10" fill="#ffffff" stroke="#3a6f9c" stroke-width="1.5"/>
          <path d="M6 8 l7 6 l7 -6" fill="none" stroke="#3a6f9c" stroke-width="1.5"/>
        </svg>
      </li>
      <li class="contact__item">www.megtarvish.co.nz
        <svg class="contact__icon" viewBox="0 0 26 26" aria-hidden="true">
          <circle cx="13" cy="13" r="12" fill="#dfe9f2"/>
          <circle cx="13" cy="13" r="8" fill="#3a8fd0"/>
          <ellipse cx="13" cy="13" rx="3.5" ry="8" fill="none" stroke="#ffffff" stroke-width="1"/>
          <line x1="5" y1="13" x2="21" y2="13" stroke="#ffffff" stroke-width="1"/>
        </svg>
      </li>
    </ul>

    <address class="address">
      MKTPR The Quarry Lodge, Level<br>
      One 48 Marlow Parade Cnr Fenwick St &amp;<br>
      Marlow Parade P O Box 38 219<br>
      WELLINGTON 6143
    </address>
  </section>
</body>
</html>
```